RiverPine - Rebranding, Namecard, Stationary and One Page Web

Refresh logo, make it modern and design matching name card, stationary and one page web

RiverPine Information Technology (Int'l) Company Limited
松河訊息科技(國際)有限公司

Company is System Integrator, and will be providing products and services to government and enterprise organizations. Our Chief Security Officer came from top U.S. vendor, and had been working on top enterprise and government projects globally, so we want the refreshed image of the new company to have a East Cost U.S. style, with hint of technology from Silicon Valley. The company will also be representing top brands from the U.S. on information security.

Branding refresh is needed because company is being acquired and is expanding

Target Market(s)

Cyber Security

Industry/Entity Type

Information Technology

Contact Information for Business Card

Need Chinese and English

Number of Pages Required

1 page

Font styles to use
Sans Serif

Colors
0292cd
00a990

Requirements
Must have
• Modern, clean, cyber look. Must keep same colors and general look and feel of original logo. Only modernization, do not change its personality

```html
<!DOCTYPE html>
<html lang="en">
<head>
<meta charset="utf-8">
<title>RiverPine Name Card</title>
<link href="https://fonts.googleapis.com/css2?family=Open+Sans:wght@400;600;700&family=Noto+Sans+TC:wght@400&display=swap" rel="stylesheet">
<style>
  :root {
    --page-bg: #1f1f1f;
    --card-bg: #2b2b2c;
    --brand-blue: #0292cd;
    --brand-green: #00a990;
    --silver: #b9bcc0;
    --text-light: #e6e6e6;
    --divider: #8a8a8a;
  }
  * { margin: 0; padding: 0; box-sizing: border-box; }
  html, body {
    width: 1200px; height: 1000px; overflow: hidden;
    background: var(--page-bg);
    font-family: "Open Sans", sans-serif;
  }
  .stage {
    width: 1200px; height: 1000px;
    display: flex; flex-direction: column; align-items: center; justify-content: center;
    gap: 40px;
  }
  .card {
    width: 760px; height: 422px;
    background: var(--card-bg);
    position: relative;
    box-shadow: 0 12px 30px rgba(0,0,0,0.45);
  }
  /* Card back */
  .card-back .wordmark {
    position: absolute; top: 150px; left: 0; right: 0;
    text-align: center;
    font-size: 44px; font-weight: 700;
    color: var(--silver);
    letter-spacing: 1px;
  }
  .card-back .company {
    position: absolute; top: 300px; left: 0; right: 0;
    text-align: center; line-height: 1.35;
  }
  .company-en { color: var(--brand-blue); font-size: 17px; letter-spacing: 0.3px; }
  .company-zh { color: var(--brand-green); font-size: 17px; font-family: "Noto Sans TC", sans-serif; }

  /* Card front */
  .card-front .wordmark {
    position: absolute; top: 138px; left: 60px;
    font-size: 44px; font-weight: 700;
    color: var(--brand-blue);
  }
  .card-front .divider {
    position: absolute; top: 110px; left: 350px;
    width: 2px; height: 124px; background: var(--divider);
  }
  .person { position: absolute; top: 104px; left: 390px; }
  .person-name { color: var(--brand-blue); font-size: 27px; font-weight: 700; line-height: 1.15; letter-spacing: 0.5px; }
  .person-role { color: var(--brand-green); font-size: 22px; font-weight: 600; line-height: 1.2; }
  .contact-list { list-style: none; margin-top: 18px; }
  .contact-list li {
    display: flex; align-items: center; gap: 14px;
    color: var(--text-light); font-size: 18px; line-height: 1.5;
  }
  .contact-list svg { width: 15px; height: 15px; fill: var(--brand-blue); flex: none; }
  .contact-list .accent { color: var(--brand-blue); }
  .address {
    position: absolute; left: 60px; top: 320px;
    display: flex; gap: 10px;
    font-size: 17px; line-height: 1.35; color: var(--text-light);
  }
  .address-label { color: var(--brand-blue); font-weight: 700; white-space: nowrap; }
</style>
</head>
<body>
<main class="stage">
  <section class="card card-back">
    <div class="wordmark">RiverPine</div>
    <div class="company">
      <p class="company-en">RiverPine Information Technology (Int'l) Company Limited</p>
      <p class="company-zh">松河訊息科技(國際)有限公司</p>
    </div>
  </section>

  <section class="card card-front">
    <div class="wordmark">RiverPine</div>
    <div class="divider"></div>
    <div class="person">
      <p class="person-name">Daniel Wong</p>
      <p class="person-role">CEO</p>
      <ul class="contact-list">
        <li>
          <svg viewBox="0 0 24 24" aria-hidden="true"><path d="M6.6 10.8a15.1 15.1 0 0 0 6.6 6.6l2.2-2.2a1 1 0 0 1 1-.25 11.4 11.4 0 0 0 3.6.57 1 1 0 0 1 1 1V20a1 1 0 0 1-1 1A17 17 0 0 1 3 4a1 1 0 0 1 1-1h3.5a1 1 0 0 1 1 1c0 1.25.2 2.45.57 3.6a1 1 0 0 1-.25 1z"/></svg>
          <span>(852) 6127 4408</span>
        </li>
        <li>
          <svg viewBox="0 0 24 24" aria-hidden="true"><path d="M2 5h20v14H2z M3 6l9 7 9-7" fill="none" stroke="#0292cd" stroke-width="2"/><path d="M2 5h20L12 13z"/></svg>
          <span>danielwong@hkriverpine.com.hk</span>
        </li>
        <li>
          <svg viewBox="0 0 24 24" aria-hidden="true"><circle cx="12" cy="12" r="10"/><path d="M2 12h20M12 2v20M5 6h14M5 18h14" stroke="#2b2b2c" stroke-width="1.5" fill="none"/></svg>
          <span>www.<span class="accent">hkriverpine</span>.com.hk</span>
        </li>
      </ul>
    </div>
    <div class="address">
      <span class="address-label">RiverPine -</span>
      <span>Room B, Unit 418, 4/F, Lok Shan Ind. Bldg,<br>No. 12 Tai Yip Lane, Kowloon Bay, Kowloon, HKSAR</span>
    </div>
  </section>
</main>
</body>
</html>
```